Valdane Companies Business Card Design

We need a new business card for our Private Equity Real Estate Development firm, “Valdane” and our EB-5 regional center “Thornmere Regional Center” on one card. We prefer a design that is simple, elegant, and represents the luxury products we design and build as well as the financial security and stability our successful history has produced. We are an industry leader in our field and 3rd generation family business that has evolved into an institutional quality investment platform. Considered design size is standard business card dimensions (3.5 x 2 inches with an additional 1/8 inch space for design elements or backgrounds that extend beyond the finished size of your piece.

Target Market(s)

• High net worth individuals
• Highly skilled technical workers and physicians in the US seeking investment-based immigration opportunities
• Sophisticated private equity investors
• Intermediary partners include domestic attorneys and investment brokers, as well as international agent networks
• US real estate developers

Industry/Entity Type

Finance

Contact Information for Business Card

(Providing placeholder info for personal information, please design for longer character spaces, longer names and addresses etc..)
• Logo for Valdane
• Logo for Thornmere Regional Center
• Full name: Marcus Valdane
• Job title: CEO
• Email address: mvaldane@valdanecompanies.com
• Cell phone number: +1.555.314.2287
• Office number +1.555.628.4410
• Office address: Larkfield Court 5, 4817 Vista Orilla, Harlow Bay, CA.
• Website: www.valdanecompanies.com

Font styles to use
Serif
Sans Serif

Colors
ec1f27
ffffff
000000

Requirements
Must have
• • Logo for Valdane
• • Logo for Thornmere Regional Center
• - Use rounded corners
• (See .ai file included for logos)
Nice to have
• • Simple, elegant design
• • Aesthetically compatible with our website design (www.valdanecompanies.com)
• • Color palette including but not limited to white, black, and red (as per logos)
Should not have
• - Not too much red color
• - Do not stack both logos on top of each other

```html
<!DOCTYPE html>
<html lang="en">
<head>
<meta charset="utf-8">
<title>Valdane Companies Business Card</title>
<link rel="stylesheet" href="https://fonts.googleapis.com/css2?family=Cinzel:wght@600;700&family=Lato:wght@400&display=swap">
<style>
  :root {
    --stage: #636363;
    --card: #2f2f2f;
    --red: #b0192e;
    --white: #ffffff;
    --muted: #e8e8e8;
    --logo-grey: #4a4a4a;
  }
  * { margin: 0; padding: 0; box-sizing: border-box; }
  html, body { width: 1200px; height: 1200px; overflow: hidden; }
  body { background: var(--stage); position: relative; font-family: "Lato", sans-serif; }

  .card {
    position: absolute;
    left: 246px;
    width: 708px;
    height: 404px;
    background: var(--card);
    border-radius: 28px;
  }
  .card--front { top: 138px; }
  .card--back { top: 663px; }

  /* Front */
  .front-brand {
    position: absolute;
    left: 0; right: 0; top: 186px;
    display: flex; align-items: center; justify-content: center; gap: 18px;
  }
  .front-brand__mark { width: 40px; height: 40px; background: var(--red); }
  .front-brand__name {
    font-family: "Cinzel", serif; font-weight: 600;
    font-size: 44px; letter-spacing: 2px; color: var(--logo-grey);
  }

  /* Back: regional center */
  .center-brand {
    position: absolute;
    left: 40px; width: 270px; top: 152px;
    display: flex; flex-direction: column; align-items: center; gap: 14px;
  }
  .center-brand__mark { width: 46px; height: 46px; background: var(--red); }
  .center-brand__name {
    font-family: "Cinzel", serif; font-weight: 700;
    font-size: 24px; line-height: 1.15; text-align: center; color: var(--red);
  }

  .divider {
    position: absolute; left: 331px; top: 87px;
    width: 1px; height: 228px; background: var(--red); opacity: .8;
  }

  /* Back: contact block */
  .contact { position: absolute; left: 354px; top: 84px; color: var(--muted); }
  .contact__name {
    font-family: "Cinzel", serif; font-weight: 700;
    font-size: 26px; color: var(--red); letter-spacing: .5px; line-height: 34px;
  }
  .contact__title { font-size: 19px; color: var(--white); line-height: 26px; }
  .contact__address { margin-top: 12px; font-size: 16px; line-height: 25px; }
  .contact__list { list-style: none; margin-top: 11px; }
  .contact__item {
    display: flex; align-items: center; gap: 14px;
    font-size: 16px; line-height: 23.5px;
  }
  .contact__icon { width: 14px; height: 14px; flex: none; }
  .contact__highlight { color: var(--red); }
</style>
</head>
<body>

<section class="card card--front">
  <div class="front-brand">
    <span class="front-brand__mark"></span>
    <span class="front-brand__name">Valdane Capital</span>
  </div>
</section>

<section class="card card--back">
  <div class="center-brand">
    <span class="center-brand__mark"></span>
    <span class="center-brand__name">Thornmere<br>Regional Center</span>
  </div>

  <div class="divider"></div>

  <div class="contact">
    <h1 class="contact__name">MARCUS VALDANE</h1>
    <p class="contact__title">CEO</p>
    <p class="contact__address">Larkfield Court 5, 4817 Vista Orilla<br>Harlow Bay, CA</p>
    <ul class="contact__list">
      <li class="contact__item">
        <svg class="contact__icon" viewBox="0 0 16 16"><path fill="#b0192e" d="M3.6 1 6 3.4 4.7 5.6c.9 2 2.4 3.5 4.4 4.5l2.2-1.3L14 11.4l-1.4 2.6C7 14 2 9 2 3.3Z"/></svg>
        <span>+1.555.314.2287</span>
      </li>
      <li class="contact__item">
        <svg class="contact__icon" viewBox="0 0 16 16"><rect x="4" y="1" width="8" height="14" rx="1.5" fill="none" stroke="#b0192e" stroke-width="1.5"/><circle cx="8" cy="12.5" r=".9" fill="#b0192e"/></svg>
        <span>+1.555.628.4410</span>
      </li>
      <li class="contact__item">
        <svg class="contact__icon" viewBox="0 0 16 16"><rect x="1" y="3" width="14" height="10" fill="#b0192e"/><path d="M1 3.5 8 9l7-5.5" fill="none" stroke="#2f2f2f" stroke-width="1.3"/></svg>
        <span>mvaldane@valdanecompanies.com</span>
      </li>
      <li class="contact__item">
        <svg class="contact__icon" viewBox="0 0 16 16" fill="none" stroke="#b0192e" stroke-width="1.2"><circle cx="8" cy="8" r="6.5"/><ellipse cx="8" cy="8" rx="3" ry="6.5"/><path d="M1.5 8h13M2.5 4.8h11M2.5 11.2h11"/></svg>
        <span>www.<span class="contact__highlight">valdanecompanies</span>.com</span>
      </li>
    </ul>
  </div>
</section>

</body>
</html>
```